Harrow Point Metrics Company Website Design and Coding

We want to redesign our existing website so that it is more visually and functionally appealing to prospective clients and potential job candidates. We would like to keep our current color scheme and implement our current logo as well. We have a high-level idea of website structure that we are thinking of, which is in the attached files. Logo is included as well. The final design would ideally be energy and analytics focused. We will need the new website to be coded as well, please.

Target Market(s)

Energy and utility industry

Industry/Entity Type

Energy/analytics

Coding

Coded - Design and coding required

Number of Pages Required

5+ page

Font styles to use
Sans Serif

Colors
0094D4
00A9DD
6FCCEA
C7EBF8
E9F6FB
F0912C
F2A743
F7CA91
FBE8D2
FDF5EE

Requirements
Must have
• Consistent color scheme- please use the one that we provided. We need an overview, a home page, and our core services. A separate job application page. Logo must be incorporated. We would like e "Meet our Team" page. Please include all of the content that is listed in our attachments.
Nice to have
• Movement
Should not have
• No music, no cartoons/animation, no pictures of a chalkboard

```html
<!DOCTYPE html>
<html lang="en">
<head>
<meta charset="utf-8">
<title>Harrow Point Metrics — Home Page Concepts</title>
<link href="https://fonts.googleapis.com/css2?family=Barlow:wght@500;600;700&family=Roboto:wght@400;500;700&display=swap" rel="stylesheet">
<style>
:root{
  --blue:#0094D4;
  --blue-2:#00A9DD;
  --sky:#6FCCEA;
  --ice:#C7EBF8;
  --mist:#E9F6FB;
  --orange:#F0912C;
  --amber:#F2A743;
  --peach:#F7CA91;
  --ink:#2f3336;
  --text:#5b6166;
  --footer:#4f5254;
  --stage:#edf4fb;
  --white:#ffffff;
}
*{box-sizing:border-box;margin:0;padding:0}
html,body{width:780px;height:1200px;overflow:hidden}
body{background:var(--stage);font-family:"Roboto",Arial,sans-serif;position:relative}
.page{position:absolute;top:58px;width:318px;height:1083px;background:var(--white);overflow:hidden;box-shadow:0 4px 14px rgba(20,60,100,.18)}
.page--classic{left:52px}
.page--topbar{left:410px}
.abs{position:absolute}

/* header */
.brand{position:absolute;left:29px;top:11px;display:flex;align-items:center;gap:3px}
.brand__dot{width:9px;height:9px;border-radius:50%;background:var(--ice)}
.brand__name{font:400 6.2px "Roboto",Arial,sans-serif;color:var(--blue)}
.nav{position:absolute;display:flex;gap:6.5px;font:500 3.3px "Roboto",Arial,sans-serif;color:var(--ink);letter-spacing:.1px}
.nav .is-active{color:var(--blue)}
.page--topbar .nav .is-active{color:var(--orange)}
.social{position:absolute;display:flex;gap:2px}
.social span{width:9px;height:9px;border-radius:50%;background:var(--white);box-shadow:0 0 2px rgba(0,0,0,.3)}
.social span:first-child{background:var(--orange)}
.topbar{position:absolute;top:0;right:0;width:165px;height:10px;background:var(--blue);clip-path:polygon(6px 0,100% 0,100% 100%,0 100%);display:flex;align-items:center;gap:4px;padding-left:14px;font:400 2.8px "Roboto",Arial,sans-serif;color:var(--white)}
.topbar .social{position:static;gap:1.5px}
.topbar .social span{width:6px;height:6px;box-shadow:none}

/* hero */
.hero{position:absolute;left:0;top:33px;width:318px;height:180px}
.hero--tablet{background:radial-gradient(circle at 78% 35%,rgba(70,120,230,.8),transparent 40%),radial-gradient(circle at 15% 30%,rgba(60,60,190,.7),transparent 45%),linear-gradient(120deg,#161a4d,#232f86 40%,#0c1233 65%,#1d3f9c)}
.hero--chart{background:radial-gradient(circle at 70% 40%,rgba(30,190,120,.55),transparent 45%),radial-gradient(circle at 25% 60%,rgba(20,120,110,.6),transparent 50%),linear-gradient(135deg,#0a2230,#0d5a4c 45%,#081a24)}
.hero__curve{position:absolute;left:0;top:0}
.hero__title{position:absolute;left:0;width:318px;top:50px;text-align:center;font:600 10px "Barlow",Arial,sans-serif;color:var(--white);letter-spacing:.3px}
.hero__lead{position:absolute;left:84px;width:150px;top:66px;text-align:center;font:500 4.3px/8px "Roboto",Arial,sans-serif;color:var(--white)}

.btn{position:absolute;height:12px;border-radius:6px;background:var(--orange);color:var(--white);display:flex;align-items:center;justify-content:center;gap:2px;font:700 3.4px "Roboto",Arial,sans-serif;letter-spacing:.1px}

.section-title{position:absolute;left:0;width:318px;text-align:center;font:600 10.5px "Barlow",Arial,sans-serif;color:var(--blue);letter-spacing:.3px}
.body-copy{position:absolute;text-align:center;font:400 3.8px/7px "Roboto",Arial,sans-serif;color:var(--text)}

/* services */
.services{position:absolute;left:0;top:311px;width:318px;height:213px;background:radial-gradient(circle at 20% 20%,rgba(255,255,255,.12),transparent 40%),linear-gradient(180deg,#0b86cf,#1592da 55%,#0a7fc6)}
.services .section-title{color:var(--white);top:21px}
.service{position:absolute;width:81px;height:67px;border:1px solid var(--white);border-radius:2px;display:flex;align-items:center;justify-content:center;text-align:center;font:700 4.3px/7.5px "Roboto",Arial,sans-serif;color:var(--white);box-shadow:0 1px 3px rgba(0,0,0,.25)}
.service--forecast{background:linear-gradient(160deg,#1d3b4a,#0f2a36 60%,#34312d)}
.service--planning{background:var(--amber);flex-direction:column;gap:4px}
.service--evaluation{background:radial-gradient(circle at 45% 35%,#3e7fa8,transparent 55%),linear-gradient(180deg,#0c2b45,#1d4f6e 60%,#4b3b2c)}
.service--pilot{background:linear-gradient(180deg,#2d4b66,#4a5970 50%,#b0714a)}
.service--portfolio{background:radial-gradient(circle at 55% 45%,#3c88a8,transparent 50%),linear-gradient(135deg,#2a3a30,#2a5c70 60%,#c28a3e)}
.service--delivery{background:linear-gradient(180deg,#0e2730,#134852 45%,#3b1d2c)}

/* team */
.member{position:absolute;top:588px;width:55px;height:59px;border:1px solid var(--blue);border-radius:3px}
.member__photo{position:absolute;left:12px;top:-12px;width:31px;height:31px;border-radius:50%;background:linear-gradient(160deg,#9aa0a5,#4d5257);border:2px solid var(--white);box-shadow:0 0 0 3px var(--white)}
.member__name{position:absolute;left:0;width:53px;top:24px;text-align:center;font:500 4.2px "Roboto",Arial,sans-serif;color:var(--blue)}
.member__role{position:absolute;left:0;width:53px;top:33px;text-align:center;font:400 3.2px "Roboto",Arial,sans-serif;color:var(--text)}
.member__link{position:absolute;left:22px;top:43px;width:10px;height:10px;border-radius:50%;background:var(--orange)}

/* careers */
.careers{position:absolute;left:0;top:676px;width:318px;height:124px;overflow:hidden}
.careers--chart{background:radial-gradient(circle at 62% 45%,rgba(40,220,150,.55),transparent 40%),linear-gradient(120deg,#0c2e3d,#0b4d52 50%,#071a22)}
.careers--tablet{background:radial-gradient(circle at 80% 60%,rgba(80,130,240,.8),transparent 40%),radial-gradient(circle at 92% 25%,rgba(240,140,60,.4),transparent 25%),linear-gradient(120deg,#1e2166,#283a98 45%,#0d1440)}
.careers__circle{position:absolute;left:21px;top:-6px;width:138px;height:138px;border-radius:50%;background:rgba(228,232,238,.9)}
.careers .section-title{width:180px;left:0;top:19px}
.careers .body-copy{left:34px;width:112px;top:39px;font-size:3.7px}

/* case study */
.case__image{position:absolute;top:853px;width:81px;height:59px}
.case__image--chart{background:linear-gradient(135deg,#d8eef2,#4fc4a0 55%,#1d6b66)}
.case__image--roads{background:radial-gradient(circle at 50% 30%,#4fa6d8,transparent 45%),linear-gradient(160deg,#1c3b5c,#3a5a7a 55%,#b36a3a)}
.case__image--land{background:linear-gradient(180deg,#c9dbe8,#a9c4d6 45%,#5c8a4c 70%,#2f5a34)}
.case__card{position:absolute;top:903px;width:76px;height:34px;background:var(--white);border-bottom:1.5px solid var(--blue);box-shadow:0 2px 4px rgba(0,0,0,.12);padding:4px 4px 0}
.case__date{font:400 3px "Roboto",Arial,sans-serif;color:var(--orange)}
.case__title{margin-top:2.5px;font:500 4.2px/7px "Roboto",Arial,sans-serif;color:var(--ink)}

/* footer */
.footer{position:absolute;left:0;top:950px}
.footer__brand{position:absolute;left:29px;top:1020px;display:flex;align-items:center;gap:3px}
.footer__brand .brand__name{color:var(--white);font-size:5.8px}
.footer__brand .brand__dot{background:#8c9194}
.footer__heading{position:absolute;top:997px;font:500 4.3px "Roboto",Arial,sans-serif;color:var(--white)}
.footer__list{position:absolute;list-style:none;font:400 3.5px "Roboto",Arial,sans-serif;color:var(--white)}
.footer__list li{display:flex;align-items:center;gap:4px;height:10.4px}
.footer__list li::before{content:"";width:3px;height:3px;border-radius:50%;background:var(--orange)}
.contact-item{position:absolute;left:154px;font:400 3px/4.6px "Roboto",Arial,sans-serif;color:var(--white);padding-left:10px}
.contact-item b{font-weight:500;font-size:3.5px}
.contact-item svg{position:absolute;left:0;top:0}
.footer__about{position:absolute;left:219px;top:1007px;width:69px;font:400 2.7px/4.6px "Roboto",Arial,sans-serif;color:var(--white);text-align:justify}
.footer__rule{position:absolute;left:29px;top:1064px;width:259px;height:1px;background:rgba(255,255,255,.2)}
.footer__copy{position:absolute;left:0;width:318px;top:1071px;text-align:center;font:400 3px "Roboto",Arial,sans-serif;color:var(--white)}
.footer__copy b{font-weight:700}
</style>
</head>
<body>

<!-- ===== Concept one: classic header ===== -->
<main class="page page--classic">
  <header>
    <div class="brand"><span class="brand__dot"></span><span class="brand__name">Harrow Point Metrics</span></div>
    <nav class="nav" style="left:117px;top:15px"><span class="is-active">HOME</span><span>CORE SERVICES</span><span>ABOUT</span><span>OUR WORK</span><span>BLOG</span><span>CONTACT US</span></nav>
    <div class="social" style="left:256px;top:12px"><span></span><span></span><span></span></div>
  </header>

  <section class="hero hero--tablet" role="img" aria-label="Photo of a hand with a stylus over a glowing analytics tablet, blue tones"></section>
  <svg class="hero__curve" width="318" height="220" viewBox="0 0 318 220" aria-hidden="true">
    <path d="M0 153 Q159 229 318 153 L318 220 L0 220 Z" fill="#fff"/>
    <path d="M0 153 Q159 251 318 153 Q159 229 0 153 Z" fill="#0094D4"/>
  </svg>
  <h1 class="hero__title">HARROW POINT METRICS</h1>
  <p class="hero__lead">Harrow Point Metrics was formed in 2016 to help utilities and regulatory agencies navigate</p>
  <a class="btn" style="left:137px;top:125px;width:43px">LEARN MORE <svg width="3.5" height="3.5" viewBox="0 0 10 10"><circle cx="5" cy="5" r="5" fill="#fff"/><path d="M3.5 2.8 6 5 3.5 7.2" stroke="#F0912C" stroke-width="1.6" fill="none"/></svg></a>

  <h2 class="section-title" style="top:220px">ABOUT US</h2>
  <p class="body-copy" style="left:44px;width:231px;top:239px">Harrow Point Metrics was formed in 2016 to help utilities and regulatory agencies navigate the technical, economic, and policy challenges of building a smarter and cleaner energy future. Through cutting edge research design and analysis methods we provide DSM program administrators with data-driven insights into how various technologies and interventions affect the way homes and businesses use energy.</p>
  <a class="btn" style="left:137px;top:277px;width:43px">LEARN MORE <svg width="3.5" height="3.5" viewBox="0 0 10 10"><circle cx="5" cy="5" r="5" fill="#fff"/><path d="M3.5 2.8 6 5 3.5 7.2" stroke="#F0912C" stroke-width="1.6" fill="none"/></svg></a>

  <section class="services">
    <h2 class="section-title">OUR SERVICES</h2>
    <div class="service service--forecast" role="img" aria-label="Service photo: city skyline with chart overlay" style="left:30px;top:49px">PREDICTIVE ANALYTICS<br>AND FORECASTING</div>
    <div class="service service--planning" style="left:119px;top:49px"><svg width="16" height="14" viewBox="0 0 16 14" aria-hidden="true"><rect x="1" y="1" width="12" height="10" fill="none" stroke="#fff" stroke-width="1"/><path d="M3 9V6M6 9V4M9 9V5" stroke="#fff" stroke-width="1.2"/><circle cx="11" cy="9" r="2.5" fill="none" stroke="#fff"/><path d="M13 11l2 2" stroke="#fff"/></svg>T&amp;D PLANNING</div>
    <div class="service service--evaluation" role="img" aria-label="Service photo: digital globe over an industrial city at night" style="left:207px;top:49px">EVALUATION</div>
    <div class="service service--pilot" role="img" aria-label="Service photo: power transmission tower at dusk" style="left:30px;top:124px">PILOT &amp; EMERGING<br>TECH SUPPORT</div>
    <div class="service service--portfolio" role="img" aria-label="Service photo: transmission tower beside a digital globe" style="left:119px;top:124px">PROGRAM PORTFOLIO &amp;<br>RESOURCE PLANNING</div>
    <div class="service service--delivery" role="img" aria-label="Service photo: server room corridor with lights" style="left:207px;top:124px">PROGRAM DELIVERY<br>SUPPORT</div>
  </section>

  <h2 class="section-title" style="top:548px">OUR TEAM</h2>
  <article class="member" style="left:29px"><div class="member__photo" role="img" aria-label="Portrait photo of team member"></div><p class="member__name">Evan Marlow, M.S.</p><p class="member__role">Partner</p><span class="member__link"></span></article>
  <article class="member" style="left:97px"><div class="member__photo" role="img" aria-label="Portrait photo of team member"></div><p class="member__name">Rafi Dunmore, M.P.P.</p><p class="member__role">Partner</p><span class="member__link"></span></article>
  <article class="member" style="left:165px"><div class="member__photo" role="img" aria-label="Portrait photo of team member"></div><p class="member__name">Clara Vennet</p><p class="member__role">Partner</p><span class="member__link"></span></article>
  <article class="member" style="left:233px"><div class="member__photo" role="img" aria-label="Portrait photo of team member"></div><p class="member__name">Nadia Roswell, M.S.</p><p class="member__role">Partner</p><span class="member__link"></span></article>

  <section class="careers careers--chart" role="img" aria-label="Photo of a hand touching a glowing green stock chart">
    <div class="careers__circle"></div>
    <h2 class="section-title">CAREERS</h2>
    <p class="body-copy">At HPM, we are driven to help create a smarter and cleaner energy future, and we are always looking for talented professionals who share our passion for achieving this goal. We are a transparent organization where you will have the opportunity to work directly with our senior energy experts.</p>
    <a class="btn" style="left:65px;top:91px;width:50px">VIEW OPENINGS <svg width="3.5" height="3.5" viewBox="0 0 10 10"><circle cx="5" cy="5" r="5" fill="#fff"/><path d="M3.5 2.8 6 5 3.5 7.2" stroke="#F0912C" stroke-width="1.6" fill="none"/></svg></a>
  </section>

  <h2 class="section-title" style="top:830px">CASE STUDY</h2>
  <div class="case__image case__image--chart" style="left:30px" role="img" aria-label="Case study photo: green financial chart"></div>
  <div class="case__image case__image--roads" style="left:119px" role="img" aria-label="Case study photo: highway interchange at night with globe"></div>
  <div class="case__image case__image--land" style="left:207px" role="img" aria-label="Case study photo: green hills with energy icons"></div>
  <article class="case__card" style="left:30px"><p class="case__date">07 Jul 2022</p><p class="case__title">Journal Articles and<br>Conference Presentations</p></article>
  <article class="case__card" style="left:119px"><p class="case__date">07 Jul 2022</p><p class="case__title">Journal Articles and<br>Conference Presentations</p></article>
  <article class="case__card" style="left:207px"><p class="case__date">07 Jul 2022</p><p class="case__title">Journal Articles and<br>Conference Presentations</p></article>

  <svg class="footer" width="318" height="133" viewBox="0 950 318 133" aria-hidden="true">
    <path d="M0 1010 Q159 918 318 1010 Q159 940 0 1010 Z" fill="#0094D4"/>
    <path d="M0 1010 Q159 940 318 1010 L318 1083 L0 1083 Z" fill="#4f5254"/>
  </svg>
  <div class="footer__brand"><span class="brand__dot"></span><span class="brand__name">Harrow Point Metrics</span></div>
  <h3 class="footer__heading" style="left:103px">QUICK LINKS</h3>
  <ul class="footer__list" style="left:103px;top:1006px"><li>Browse Writing Jobs</li><li>Hire Writers</li><li>Contact</li><li>Sign Up</li><li>Login</li></ul>
  <h3 class="footer__heading" style="left:154px">CONTACT INFO</h3>
  <p class="contact-item" style="top:1008px"><svg width="4" height="5" viewBox="0 0 8 10"><path d="M4 10C1 6 0 5 0 4a4 4 0 0 1 8 0c0 1-1 2-4 6z" fill="#F0912C"/><circle cx="4" cy="4" r="1.4" fill="#4f5254"/></svg><b>ADDRESS:</b><br>48 Larkspur Row<br>Suite B2 Fairhaven, GA 30999</p>
  <p class="contact-item" style="top:1032px"><svg width="4" height="4" viewBox="0 0 10 10"><path d="M2 0l2 3-1 1.5c1 1.5 1.5 2 3 3L7.5 6l2.5 2-1 2C4 10 0 6 0 1z" fill="#F0912C"/></svg><b>PHONE:</b><br>555.014.2286</p>
  <p class="contact-item" style="top:1048px"><svg width="4.5" height="3.5" viewBox="0 0 10 8"><rect width="10" height="8" fill="#F0912C"/><path d="M0 0l5 4 5-4" stroke="#4f5254" fill="none"/></svg><b>EMAIL:</b><br>info@harrowpointmetrics.com</p>
  <h3 class="footer__heading" style="left:219px">GET IN TOUCH</h3>
  <p class="footer__about">Harrow Point Metrics (HPM) was formed in 2016 to help utilities and regulatory agencies navigate the technical, economic, and policy challenges of building a smarter and cleaner energy future.</p>
  <a class="btn" style="left:219px;top:1036px;width:33px;height:9px;font-size:2.8px"><svg width="3.5" height="3" viewBox="0 0 10 8"><rect width="10" height="8" fill="#fff"/><path d="M0 0l5 4 5-4" stroke="#F0912C" fill="none"/></svg>CONTACT US</a>
  <div class="footer__rule"></div>
  <p class="footer__copy">© 2022 <b>HARROW POINT METRICS</b> &nbsp;| &nbsp;All Rights Reserved</p>
  <div class="social" style="left:256px;top:1068px"><span></span><span></span><span></span></div>
</main>

<!-- ===== Concept two: header with contact bar ===== -->
<main class="page page--topbar">
  <header>
    <div class="topbar"><span>555.014.2286 &nbsp;| &nbsp;info@harrowpointmetrics.com</span><span class="social"><span></span><span></span><span></span></span></div>
    <div class="brand"><span class="brand__dot"></span><span class="brand__name">Harrow Point Metrics</span></div>
    <nav class="nav" style="left:136px;top:20px;gap:9px"><span class="is-active">HOME</span><span>CORE SERVICES</span><span>ABOUT</span><span>OUR WORK</span><span>BLOG</span><span>CONTACT US</span></nav>
  </header>

  <section class="hero hero--chart" role="img" aria-label="Photo of a hand touching a glowing green stock chart"></section>
  <svg class="hero__curve" width="318" height="220" viewBox="0 0 318 220" aria-hidden="true">
    <path d="M0 153 Q159 229 318 153 L318 220 L0 220 Z" fill="#fff"/>
    <path d="M0 153 Q159 251 318 153 Q159 229 0 153 Z" fill="#0094D4"/>
  </svg>
  <h1 class="hero__title">HARROW POINT METRICS</h1>
  <p class="hero__lead">Harrow Point Metrics was formed in 2016 to help utilities and regulatory agencies navigate</p>
  <a class="btn" style="left:137px;top:125px;width:43px">LEARN MORE <svg width="3.5" height="3.5" viewBox="0 0 10 10"><circle cx="5" cy="5" r="5" fill="#fff"/><path d="M3.5 2.8 6 5 3.5 7.2" stroke="#F0912C" stroke-width="1.6" fill="none"/></svg></a>

  <h2 class="section-title" style="top:220px">ABOUT US</h2>
  <p class="body-copy" style="left:44px;width:231px;top:239px">Harrow Point Metrics was formed in 2016 to help utilities and regulatory agencies navigate the technical, economic, and policy challenges of building a smarter and cleaner energy future. Through cutting edge research design and analysis methods we provide DSM program administrators with data-driven insights into how various technologies and interventions affect the way homes and businesses use energy.</p>
  <a class="btn" style="left:137px;top:277px;width:43px">LEARN MORE <svg width="3.5" height="3.5" viewBox="0 0 10 10"><circle cx="5" cy="5" r="5" fill="#fff"/><path d="M3.5 2.8 6 5 3.5 7.2" stroke="#F0912C" stroke-width="1.6" fill="none"/></svg></a>

  <section class="services">
    <h2 class="section-title">OUR SERVICES</h2>
    <div class="service service--forecast" role="img" aria-label="Service photo: city skyline with chart overlay" style="left:30px;top:49px">PREDICTIVE ANALYTICS<br>AND FORECASTING</div>
    <div class="service service--planning" style="left:119px;top:49px"><svg width="16" height="14" viewBox="0 0 16 14" aria-hidden="true"><rect x="1" y="1" width="12" height="10" fill="none" stroke="#fff" stroke-width="1"/><path d="M3 9V6M6 9V4M9 9V5" stroke="#fff" stroke-width="1.2"/><circle cx="11" cy="9" r="2.5" fill="none" stroke="#fff"/><path d="M13 11l2 2" stroke="#fff"/></svg>T&amp;D PLANNING</div>
    <div class="service service--evaluation" role="img" aria-label="Service photo: digital globe over an industrial city at night" style="left:207px;top:49px">EVALUATION</div>
    <div class="service service--pilot" role="img" aria-label="Service photo: power transmission tower at dusk" style="left:30px;top:124px">PILOT &amp; EMERGING<br>TECH SUPPORT</div>
    <div class="service service--portfolio" role="img" aria-label="Service photo: transmission tower beside a digital globe" style="left:119px;top:124px">PROGRAM PORTFOLIO &amp;<br>RESOURCE PLANNING</div>
    <div class="service service--delivery" role="img" aria-label="Service photo: server room corridor with lights" style="left:207px;top:124px">PROGRAM DELIVERY<br>SUPPORT</div>
  </section>

  <h2 class="section-title" style="top:548px">OUR TEAM</h2>
  <article class="member" style="left:29px"><div class="member__photo" role="img" aria-label="Portrait photo of team member"></div><p class="member__name">Evan Marlow, M.S.</p><p class="member__role">Partner</p><span class="member__link"></span></article>
  <article class="member" style="left:97px"><div class="member__photo" role="img" aria-label="Portrait photo of team member"></div><p class="member__name">Rafi Dunmore, M.P.P.</p><p class="member__role">Partner</p><span class="member__link"></span></article>
  <article class="member" style="left:165px"><div class="member__photo" role="img" aria-label="Portrait photo of team member"></div><p class="member__name">Clara Vennet</p><p class="member__role">Partner</p><span class="member__link"></span></article>
  <article class="member" style="left:233px"><div class="member__photo" role="img" aria-label="Portrait photo of team member"></div><p class="member__name">Nadia Roswell, M.S.</p><p class="member__role">Partner</p><span class="member__link"></span></article>

  <section class="careers careers--tablet" role="img" aria-label="Photo of a hand with a stylus over a glowing analytics tablet">
    <div class="careers__circle"></div>
    <h2 class="section-title">CAREERS</h2>
    <p class="body-copy">At HPM, we are driven to help create a smarter and cleaner energy future, and we are always looking for talented professionals who share our passion for achieving this goal. We are a transparent organization where you will have the opportunity to work directly with our senior energy experts.</p>
    <a class="btn" style="left:65px;top:91px;width:50px">VIEW OPENINGS <svg width="3.5" height="3.5" viewBox="0 0 10 10"><circle cx="5" cy="5" r="5" fill="#fff"/><path d="M3.5 2.8 6 5 3.5 7.2" stroke="#F0912C" stroke-width="1.6" fill="none"/></svg></a>
  </section>

  <h2 class="section-title" style="top:830px">CASE STUDY</h2>
  <div class="case__image case__image--chart" style="left:30px" role="img" aria-label="Case study photo: green financial chart"></div>
  <div class="case__image case__image--roads" style="left:119px" role="img" aria-label="Case study photo: highway interchange at night with globe"></div>
  <div class="case__image case__image--land" style="left:207px" role="img" aria-label="Case study photo: green hills with energy icons"></div>
  <article class="case__card" style="left:30px"><p class="case__date">07 Jul 2022</p><p class="case__title">Journal Articles and<br>Conference Presentations</p></article>
  <article class="case__card" style="left:119px"><p class="case__date">07 Jul 2022</p><p class="case__title">Journal Articles and<br>Conference Presentations</p></article>
  <article class="case__card" style="left:207px"><p class="case__date">07 Jul 2022</p><p class="case__title">Journal Articles and<br>Conference Presentations</p></article>

  <svg class="footer" width="318" height="133" viewBox="0 950 318 133" aria-hidden="true">
    <path d="M0 1010 Q159 918 318 1010 Q159 940 0 1010 Z" fill="#0094D4"/>
    <path d="M0 1010 Q159 940 318 1010 L318 1083 L0 1083 Z" fill="#4f5254"/>
  </svg>
  <div class="footer__brand"><span class="brand__dot"></span><span class="brand__name">Harrow Point Metrics</span></div>
  <h3 class="footer__heading" style="left:103px">QUICK LINKS</h3>
  <ul class="footer__list" style="left:103px;top:1006px"><li>Browse Writing Jobs</li><li>Hire Writers</li><li>Contact</li><li>Sign Up</li><li>Login</li></ul>
  <h3 class="footer__heading" style="left:154px">CONTACT INFO</h3>
  <p class="contact-item" style="top:1008px"><svg width="4" height="5" viewBox="0 0 8 10"><path d="M4 10C1 6 0 5 0 4a4 4 0 0 1 8 0c0 1-1 2-4 6z" fill="#F0912C"/><circle cx="4" cy="4" r="1.4" fill="#4f5254"/></svg><b>ADDRESS:</b><br>48 Larkspur Row<br>Suite B2 Fairhaven, GA 30999</p>
  <p class="contact-item" style="top:1032px"><svg width="4" height="4" viewBox="0 0 10 10"><path d="M2 0l2 3-1 1.5c1 1.5 1.5 2 3 3L7.5 6l2.5 2-1 2C4 10 0 6 0 1z" fill="#F0912C"/></svg><b>PHONE:</b><br>555.014.2286</p>
  <p class="contact-item" style="top:1048px"><svg width="4.5" height="3.5" viewBox="0 0 10 8"><rect width="10" height="8" fill="#F0912C"/><path d="M0 0l5 4 5-4" stroke="#4f5254" fill="none"/></svg><b>EMAIL:</b><br>info@harrowpointmetrics.com</p>
  <h3 class="footer__heading" style="left:219px">GET IN TOUCH</h3>
  <p class="footer__about">Harrow Point Metrics (HPM) was formed in 2016 to help utilities and regulatory agencies navigate the technical, economic, and policy challenges of building a smarter and cleaner energy future.</p>
  <a class="btn" style="left:219px;top:1036px;width:33px;height:9px;font-size:2.8px"><svg width="3.5" height="3" viewBox="0 0 10 8"><rect width="10" height="8" fill="#fff"/><path d="M0 0l5 4 5-4" stroke="#F0912C" fill="none"/></svg>CONTACT US</a>
  <div class="footer__rule"></div>
  <p class="footer__copy">© 2022 <b>HARROW POINT METRICS</b> &nbsp;| &nbsp;All Rights Reserved</p>
  <div class="social" style="left:256px;top:1068px"><span></span><span></span><span></span></div>
</main>

</body>
</html>
```